Im open to ideas.. I was thinking on my business cards aswell as my logo. a place for my name. email. phone number and abn..

ive attched a file with my business logo. which i dont love the colours.. i was think a dark background with charcoal letters so something along those colour schumes but im open to ideas..

BRM Constructions

```html
<!DOCTYPE html>
<html lang="en">
<head>
<meta charset="utf-8">
<title>BRM Constructions – Business Cards</title>
<link rel="stylesheet" href="https://fonts.googleapis.com/css2?family=Source+Sans+3:wght@400;600;700&display=swap">
<style>
  :root {
    --stage: #e9e7e4;
    --charcoal: #4d4d4d;
    --black: #000000;
    --logo-light: #9b9b9b;
    --logo-dark: #5c5c5c;
    --text-strong: #d4d4d4;
    --text-soft: #c4c4c4;
    --icon: #bdbdbd;
  }
  * { box-sizing: border-box; margin: 0; padding: 0; }
  html, body {
    width: 1200px; height: 900px; overflow: hidden;
    background: var(--stage);
    font-family: "Source Sans 3", "Myriad Pro", Arial, sans-serif;
  }
  .canvas { position: relative; width: 1200px; height: 900px; }

  .card { position: absolute; overflow: hidden; box-shadow: 0 6px 18px rgba(0,0,0,.18); }

  /* Front */
  .card--front { left: 78px; top: 34px; width: 588px; height: 364px; background: var(--black); }
  .card--front .brand-band {
    height: 156px; background: var(--charcoal);
    display: flex; align-items: flex-end; padding: 0 0 26px 32px;
  }
  .brand-name {
    font-weight: 700; letter-spacing: 1px; text-transform: uppercase;
    line-height: 1;
  }
  .card--front .brand-name { color: var(--logo-light); font-size: 36px; }

  .contact-block { padding: 14px 0 0 34px; color: var(--text-soft); }
  .person-name { color: var(--text-strong); font-size: 21px; font-weight: 600; line-height: 1.2; }
  .person-role { font-size: 15.5px; line-height: 1.2; }
  .abn { font-size: 15.5px; font-weight: 600; margin-top: 18px; }
  .contact-list { list-style: none; margin-top: 14px; }
  .contact-list li {
    display: flex; align-items: center; gap: 8px;
    font-size: 15.5px; height: 24.5px;
  }
  .contact-list svg { width: 11px; height: 11px; fill: var(--icon); flex: none; }

  /* Back */
  .card--back { left: 388px; top: 506px; width: 567px; height: 351px; background: var(--charcoal); }
  .card--back .brand-strip {
    position: absolute; left: 0; top: 100px; width: 100%; height: 159px;
    background: var(--black);
    display: flex; align-items: center; justify-content: center;
  }
  .card--back .brand-name { color: var(--logo-dark); font-size: 38px; }
</style>
</head>
<body>
<main class="canvas">

  <section class="card card--front" aria-label="Business card front">
    <div class="brand-band">
      <span class="brand-name">BRM Constructions</span>
    </div>
    <div class="contact-block">
      <p class="person-name">Daniel Hart</p>
      <p class="person-role">Managing Director</p>
      <p class="abn">ABN NO: 12345</p>
      <ul class="contact-list">
        <li>
          <svg viewBox="0 0 24 24" aria-hidden="true"><path d="M6.6 10.8a15.1 15.1 0 0 0 6.6 6.6l2.2-2.2a1 1 0 0 1 1-.25 11.4 11.4 0 0 0 3.6.57 1 1 0 0 1 1 1V20a1 1 0 0 1-1 1A17 17 0 0 1 3 4a1 1 0 0 1 1-1h3.5a1 1 0 0 1 1 1c0 1.25.2 2.45.57 3.57a1 1 0 0 1-.25 1z"/></svg>
          (044)-555-0182
        </li>
        <li>
          <svg viewBox="0 0 24 24" aria-hidden="true"><path d="M2 5h20v14H2z M2 5l10 8 10-8" stroke="#000" stroke-width="1.6"/></svg>
          hello@brmbuild.com
        </li>
        <li>
          <svg viewBox="0 0 24 24" aria-hidden="true"><circle cx="12" cy="12" r="11"/><path d="M1 12h22M12 1c3.5 3 3.5 19 0 22M12 1c-3.5 3-3.5 19 0 22" stroke="#000" stroke-width="1.4" fill="none"/></svg>
          www.brmbuild.com
        </li>
      </ul>
    </div>
  </section>

  <section class="card card--back" aria-label="Business card back">
    <div class="brand-strip">
      <span class="brand-name">BRM Constructions</span>
    </div>
  </section>

</main>
</body>
</html>
```